Yard sign

Looking for a yard sign. <br/>Something simple, name, number. <br/>Large text, readable from 50 feet away. <br/><br/>18 x 24 inches.

Target Market(s)

Potential homeowners thinking about going solar.

Colors

Designer to choose colors to be used in the design.

Requirements
Must have
• "WE'VE GONE SOLAR!"
Nice to have
• We are a solar company, we would like a design that compliments the homeowners decision that they went solar and encourages others to do the same.

```html
<!DOCTYPE html>
<html lang="en">
<head>
<meta charset="utf-8">
<title>Lumen Solar Yard Sign</title>
<link href="https://fonts.googleapis.com/css2?family=Oswald:wght@500;600&family=Montserrat:wght@400&family=Roboto+Condensed:wght@700&family=Roboto:wght@700&display=swap" rel="stylesheet">
<style>
  :root {
    --backdrop: #1c1819;
    --sign-orange: #f66522;
    --brand-orange: #f5891f;
    --sun-yellow: #fcc427;
    --name-yellow: #fdcb43;
    --sky-top: #1d2d62;
    --sky-bottom: #4a6aa8;
    --panel-dark: #111a2e;
    --white: #ffffff;
    --ink: #0b0b0b;
  }
  * { margin: 0; padding: 0; box-sizing: border-box; }
  html, body {
    width: 1200px; height: 1200px; overflow: hidden;
    background: var(--backdrop);
  }
  .canvas { position: relative; width: 1200px; height: 1200px; }
  .yard-sign {
    position: absolute; left: 212px; top: 66px;
    width: 779px; height: 1039px;
    background: var(--sign-orange);
    overflow: hidden;
    box-shadow: 0 14px 24px rgba(0,0,0,0.45);
  }
  .hero-photo {
    position: absolute; left: 0; top: 0; width: 779px; height: 560px;
    background:
      linear-gradient(160deg, transparent 45%, rgba(17,26,46,0.85) 46%, var(--panel-dark) 80%),
      linear-gradient(180deg, var(--sky-top) 0%, var(--sky-bottom) 60%);
  }
  .wave-band { position: absolute; left: 0; top: 0; width: 779px; height: 1039px; }
  .brand-block {
    position: absolute; left: 181px; width: 600px;
    text-align: center;
  }
  .brand-name {
    position: absolute; left: 0; width: 600px; top: 217px;
    text-align: center; white-space: nowrap;
    font-family: 'Oswald', sans-serif; font-weight: 600;
    font-size: 100px; line-height: 1;
    color: var(--brand-orange);
  }
  .solar-message {
    position: absolute; left: 0; width: 600px; top: 318px;
    text-align: center; white-space: nowrap;
    font-family: 'Montserrat', sans-serif; font-weight: 400;
    font-size: 40px; line-height: 1; letter-spacing: 3px;
    color: var(--sun-yellow);
  }
  .rep-name {
    position: absolute; left: 0; width: 779px; top: 612px;
    text-align: center; white-space: nowrap;
    font-family: 'Oswald', sans-serif; font-weight: 500;
    font-size: 118px; line-height: 1;
    color: var(--name-yellow);
  }
  .phone-line {
    position: absolute; left: 0; width: 779px; top: 765px;
    display: flex; align-items: center; justify-content: center; gap: 14px;
  }
  .phone-icon { width: 80px; height: 80px; flex: none; }
  .phone-number {
    font-family: 'Roboto Condensed', sans-serif; font-weight: 700;
    font-size: 104px; line-height: 1; color: var(--white); white-space: nowrap;
  }
  .divider {
    position: absolute; left: 251px; top: 887px;
    width: 276px; height: 2px; background: var(--sun-yellow);
  }
  .website {
    position: absolute; left: 0; width: 779px; top: 914px;
    text-align: center; white-space: nowrap;
    font-family: 'Roboto', sans-serif; font-weight: 700;
    font-size: 62px; line-height: 1; color: var(--ink);
  }
</style>
</head>
<body>
<div class="canvas">
  <div class="yard-sign">
    <div class="hero-photo" role="img" aria-label="Photo of a house roof covered with dark solar panels under a blue evening sky"></div>
    <svg class="wave-band" viewBox="0 0 779 1039" aria-hidden="true">
      <path d="M0 448 Q380 560 779 458 L779 511 Q380 640 0 448 Z" fill="var(--sun-yellow)"/>
      <path d="M0 448 Q380 640 779 511 L779 1039 L0 1039 Z" fill="var(--sign-orange)"/>
    </svg>
    <div class="brand-block">
      <div class="brand-name">LUMEN SOLAR</div>
      <div class="solar-message">WE'VE GONE SOLAR!</div>
    </div>
    <div class="rep-name">MARCUS HALE</div>
    <div class="phone-line">
      <svg class="phone-icon" viewBox="0 0 80 80" aria-hidden="true">
        <circle cx="40" cy="40" r="36" fill="none" stroke="var(--sun-yellow)" stroke-width="5"/>
        <path d="M24 27c2-4 6-5 8-3l4 6c1 2 0 4-2 5l-2 1c2 5 6 9 11 11l1-2c1-2 3-3 5-2l6 4c2 2 1 6-3 8-4 2-10 1-17-5-8-7-12-15-11-23z" fill="var(--white)"/>
        <path d="M44 22a14 14 0 0 1 14 14M44 15a21 21 0 0 1 21 21M44 29a7 7 0 0 1 7 7" fill="none" stroke="var(--white)" stroke-width="2.5" stroke-linecap="round"/>
      </svg>
      <span class="phone-number">200-555-0187</span>
    </div>
    <div class="divider"></div>
    <div class="website">www.lumensolar.net</div>
  </div>
</div>
</body>
</html>
```